Weekly Newsletter template for our niche within the Telecom Industry

We need a 'skeleton' format where we can insert our weekly information and ads.
We will do all the content in-house.
Content in both info and ads must be able to contain hyperlinks.
Our company website is: www. halvorsen-quibb.com
We think we would like something similar to the top format but with the single bar on the right side as a place to insert ads
Thank you.

```html
<!DOCTYPE html>
<html lang="en">
<head>
<meta charset="utf-8">
<title>Halvorsen Quibb – Telecom Regulatory Newsletter</title>
<link href="https://fonts.googleapis.com/css2?family=Poppins:wght@400;500;600;700&display=swap" rel="stylesheet">
<style>
  :root{
    --header-top:#e6f3f8;
    --header-bottom:#f4f9fb;
    --ink:#111418;
    --body-text:#5a5f66;
    --link:#1a7fd4;
    --side-top:#17a4be;
    --side-mid:#8fba88;
    --side-bottom:#cfc33a;
    --white:#ffffff;
    --footer:#1d2630;
    --ad-top:#a9cfe6;
    --ad-bottom:#5c7fa8;
    --ad-label:#e4f1f7;
  }
  *{box-sizing:border-box;margin:0;padding:0}
  html,body{width:1200px;height:2178px;overflow:hidden}
  body{position:relative;background:var(--white);font-family:"Poppins",sans-serif;color:var(--ink)}
  a{color:inherit}
  .masthead{position:absolute;left:0;top:0;width:1200px;height:408px;
    background:linear-gradient(180deg,var(--header-top),var(--header-bottom))}
  .brand{position:absolute;left:60px;top:62px;display:flex;align-items:center;gap:16px}
  .brand-mark{width:40px;height:40px;border-radius:50%;background:var(--side-top)}
  .brand-name{font-size:30px;font-weight:500;letter-spacing:0.5px;color:var(--ink)}
  .issue-date{position:absolute;right:60px;top:56px;font-size:27px;font-weight:400;color:#333}
  .masthead-title{position:absolute;left:0;width:1200px;top:162px;text-align:center;
    font-size:48px;font-weight:500;line-height:57px}

  .article{position:absolute;left:60px;top:470px;width:552px;hyphens:auto;-webkit-hyphens:auto}
  .article h2{font-size:27px;font-weight:600;line-height:40px;margin-bottom:26px;hyphens:none;-webkit-hyphens:none}
  .article p{font-size:20.5px;line-height:36px;color:var(--body-text);margin-bottom:13px}
  .article p.spaced{margin-top:22px}
  .article a{color:var(--link);font-weight:600;text-decoration:none;word-break:break-all}

  .rail{position:absolute;left:663px;top:328px;width:477px;display:flex;flex-direction:column}
  .sidebar{padding:36px 30px 22px;hyphens:auto;-webkit-hyphens:auto;
    background:linear-gradient(180deg,var(--side-top) 0%,var(--side-mid) 55%,var(--side-bottom) 100%);
    color:var(--white)}
  .sidebar h3{font-size:27px;font-weight:700;line-height:40px;text-transform:uppercase;margin-bottom:18px;hyphens:none;-webkit-hyphens:none}
  .sidebar .kicker{font-size:19px;line-height:36px;margin-bottom:12px}
  .sidebar .kicker.caps{text-transform:uppercase}
  .sidebar p{font-size:20.5px;line-height:36px;margin-bottom:24px}
  .sidebar a{font-weight:600;text-decoration:underline;word-break:break-all}
  .ad-slot{position:relative;margin-top:22px;height:375px;
    background:linear-gradient(160deg,var(--ad-top),var(--ad-bottom))}
  .ad-label{position:absolute;right:0;top:0;background:var(--ad-label);font-size:20px;padding:4px 18px;color:var(--ink)}
  .ad-caption{margin-top:20px;font-size:25px;color:var(--ink)}

  .footer{position:absolute;left:0;top:2108px;width:1200px;height:70px;background:var(--footer);
    color:var(--white);font-size:20px;display:flex;align-items:center;justify-content:center}
  .footer .page-code{position:absolute;right:34px}
</style>
</head>
<body>
  <header class="masthead">
    <div class="brand"><span class="brand-mark"></span><span class="brand-name">Halvorsen Quibb</span></div>
    <div class="issue-date">October 24, 2024</div>
    <h1 class="masthead-title">News and Information from the U.S.<br>telecom Regulatory world</h1>
  </header>

  <article class="article">
    <h2>FCC Releases Request for Comment on Proposed Rule on Unlawful Robocalls and Call Blocking</h2>
    <p>FCC Releases Request for Comment on Proposed Rule on Unlawful Robocalls and Call Blocking</p>
    <p>Comments are due by Aug. 31, 2020.</p>
    <p>The Federal Communications Commission is proceeding with a proposed rule on revisions to its rules implementing the Telephone Robocall Abuse Criminal Enforcement and Deterrence Act (TRACED Act) in a request for comment announced Friday .</p>
    <p>In advance of Friday’s proposed rule, the FCC on July 16 voted to adopt an order on call blocking and labeling that includes two safe harbors for voice service providers and some protections for legitimate calls, Nexa Creditors Forum previously reported.</p>
    <p class="spaced">During the meeting, the FCC also issued a Further Notice of Proposed Rulemaking (FNPRM) seeking comment on additional steps to protect consumers from robocalls and better inform them about provider blocking efforts. The notice specifically seeks comment on whether to obligate phone companies to better police their networks against illegal calls, and whether to require them to provide information about blocked calls to consumers for free. In addition, the notice seeks comment on notification and effective redress mechanisms for callers when their calls are blocked, and on whether measures are necessary to address the mislabeling of calls.</p>
    <p class="spaced">The July 31 proposed rule is a summary of the commission’s fourth FNPRM, in CG Docket No. 17-59, FCC 20-96, adopted on July 16, 2020, and released on July 17, 2020.</p>
    <p class="spaced">The contents of it were discussed in the open hearing and an FCC press release , providing insight into changes that were made from the draft.</p>
    <p class="spaced">Comments, identified by CG Docket No. 17-59, may be submitted online at <a href="http://apps.regwire.org/ecfs/">http://apps.regwire.org/ecfs/ .</a></p>
  </article>

  <div class="rail">
    <aside class="sidebar">
      <h3>FCC Grants Safe Harbor for Robo Call Blocking</h3>
      <div class="kicker caps">FCC Grants Safe Harbor for Robo Call Blocking</div>
      <div class="kicker">July 2020</div>
      <p>The Federal Communications Commission (FCC) has now approved “two safe harbors from liability for the unintended or inadvertent blocking of wanted calls, thus eliminating a concern that kept some companies from implementing robust robocall blocking efforts.”<a href="https://docs.regwire.org/attachments/DOC-482917A1.pdf">(https://docs.regwire.org/attachments/DOC-482917A1.pdf).</a></p>
      <p>The two safe harbors “are meant to provide further assurance to phone companies and allow them to strengthen their efforts in the battle against illegal and unwanted robocalls.” The FCC’s decision further implements provisions of the Harlow-Brenner TRACED Act which became law last December.</p>
      <p>The first safe harbor will protect phone companies that “use reasonable analytics, including caller ID authentication information, to identify and block illegal or unwanted calls from liability.”</p>
    </aside>
    <div class="ad-slot" role="img" aria-label="Advertisement image: hand touching a glowing digital circuit network">
      <span class="ad-label">Ads</span>
    </div>
    <div class="ad-caption">Robocalls are back</div>
  </div>

  <footer class="footer">
    <span>© 2024 halvorsen-quibb.com. All rights reserved.</span>
    <span class="page-code">C37</span>
  </footer>
</body>
</html>
```